Business Card, A4 Letter Head and DL Envelope for Brandvelle

We are looking for a design for our Business Card, A4 Letter Head and DL Envelope.

Brandvelle is a distributor of promotional products. We specialize in a range of branded promotional products, these include pens, polo shirts, key rings, drink bottles, uniforms and bags to name a few. We are experts in marketing and assist companies in choosing the right promotional product for their needs. We will predominately be an online business where customers visit our website and browse our range of promotional products and branding options.

Our colours are black, red, white and grey.

Files must be supplied in eps, pdf and ai format.

Please display the following information:
Derek Halloway
Account Manager
Suite xxx, 212 Ferrow Lane Melbourne, Victoria 3000
Phone +61 3 5550 1827
Mobile +61 455 016 342
sales@brandvelle-example.com.au
www.brandvelle-example.com.au

```html
<!DOCTYPE html>
<html lang="en">
<head>
<meta charset="utf-8">
<title>Brandvelle Stationery</title>
<link href="https://fonts.googleapis.com/css2?family=Montserrat:wght@600;700&family=Open+Sans:wght@400;600&family=Dancing+Script:wght@500&display=swap" rel="stylesheet">
<style>
:root{
  --red:#c4161c;
  --red-dark:#7e0c10;
  --red-deep:#5e080b;
  --ink:#3a3a3a;
  --grey:#6b6b6b;
  --grey-light:#d9d9d9;
  --paper:#ffffff;
  --stage:#ececec;
  --black:#111111;
}
*{box-sizing:border-box;margin:0;padding:0}
html,body{width:1200px;height:1024px;overflow:hidden}
body{background:var(--stage);font-family:"Open Sans",Arial,sans-serif;color:var(--ink);position:relative}
.item{position:absolute;overflow:hidden;box-shadow:0 3px 10px rgba(0,0,0,.25)}

/* brand name */
.brand{display:flex;align-items:center;gap:6px;font-family:"Montserrat",Arial,sans-serif;font-weight:700;color:var(--ink);letter-spacing:.5px;white-space:nowrap}
.brand .dot{border-radius:50%;background:var(--red);flex:none}
.brand--light{color:#fff}
.brand--light .dot{background:#fff}

.contact{font-size:6.2px;line-height:1.45;color:var(--grey)}
.contact .row{display:flex;align-items:center;gap:3px}
.contact svg{width:5px;height:5px;fill:var(--red);flex:none}
.contact .addr{margin-top:4px}

.footer-band{position:absolute;left:0;right:0;background:linear-gradient(90deg,var(--red-dark),var(--red) 50%,var(--red-dark));color:#fff;text-align:center;font-size:6.5px;font-weight:600}
.footer-band::before{content:"";position:absolute;left:0;right:0;top:-3px;height:1px;background:var(--grey-light)}

/* soft decorative tone area, no shape */
.tone-area{position:absolute}

/* letterhead */
.letterhead{width:346px;height:488px;top:30px;background:var(--paper)}
.letterhead--one{left:38px}
.letterhead--two{left:426px}
.letterhead .brand{position:absolute;left:22px;top:92px;font-size:15px}
.letterhead .brand .dot{width:12px;height:12px}
.letterhead .divider{position:absolute;left:205px;top:22px;width:1px;height:100px;background:var(--red)}
.letterhead .contact{position:absolute;left:215px;top:40px}
.letterhead .tone-area{right:0;bottom:30px;width:160px;height:260px;background:linear-gradient(90deg,rgba(196,22,28,0),rgba(196,22,28,.07))}
.letter-body{position:absolute;left:22px;top:170px;width:300px;font-size:6.1px;line-height:1.45;color:#444}
.letter-body p{margin-bottom:6px}
.signature{position:absolute;left:22px;top:404px}
.signature .name{font-family:"Dancing Script",cursive;font-size:11px;color:#333}
.signature .role{font-size:5.8px;color:#555}
.letterhead .footer-band{bottom:8px;height:14px;line-height:14px}

/* cover */
.cover{left:816px;top:30px;width:343px;height:488px;background:linear-gradient(160deg,var(--red),var(--red-dark) 85%)}
.cover .brand{position:absolute;left:0;right:0;top:128px;justify-content:center;font-size:24px}
.cover .brand .dot{width:20px;height:20px}
.cover .tone-area{left:0;right:0;top:190px;height:250px;background:linear-gradient(180deg,rgba(255,255,255,0),rgba(255,255,255,.08) 50%,rgba(255,255,255,0))}
.cover .url{position:absolute;left:0;right:0;bottom:24px;text-align:center;color:#fff;font-size:7.5px}

/* business cards */
.card{top:542px;height:183px;border-radius:14px}
.card--front{left:50px;width:317px;background:var(--paper)}
.card--front .brand{position:absolute;left:18px;top:80px;font-size:13px}
.card--front .brand .dot{width:10px;height:10px}
.card--front .divider{position:absolute;left:172px;top:36px;width:1px;height:72px;background:var(--grey-light)}
.card--front .person{position:absolute;left:180px;top:45px}
.person .name{font-family:"Montserrat",Arial,sans-serif;font-weight:700;font-size:10.5px;color:var(--red)}
.person .title{font-size:7px;color:var(--grey)}
.card--front .contact{position:absolute;left:180px;top:88px;font-size:7px}
.card--front .contact svg{width:6px;height:6px}
.card--front .footer-band{bottom:8px;height:12px;line-height:12px;font-size:6.5px}
.card--dark{left:428px;width:321px;background:linear-gradient(135deg,#2b2b2b,var(--black) 60%)}
.card--red{left:827px;width:321px;background:linear-gradient(135deg,var(--red),var(--red-dark) 85%)}
.card .tone-area{left:0;top:0;bottom:0;width:180px}
.card--dark .tone-area{background:linear-gradient(90deg,rgba(255,255,255,.10),rgba(255,255,255,0))}
.card--red .tone-area{background:linear-gradient(90deg,rgba(255,255,255,.12),rgba(255,255,255,0))}
.card .back-text{position:absolute;right:14px;top:110px;text-align:right}
.card .back-text .brand{font-size:14px;justify-content:flex-end}
.card .back-text .brand .dot{width:10px;height:10px}
.card .back-text .url{color:#fff;font-size:7px}

/* envelopes */
.envelope{top:742px;height:256px}
.envelope--front{left:19px;width:373px;background:var(--paper)}
.envelope--front .brand{position:absolute;left:22px;top:78px;font-size:14px}
.envelope--front .brand .dot{width:11px;height:11px}
.envelope--front .contact{position:absolute;left:246px;top:38px}
.envelope--front .window{position:absolute;left:22px;top:124px;width:150px;height:48px;border:1px solid #bdbdbd;border-radius:5px;background:linear-gradient(#f7f7f7,#e6e6e6)}
.envelope--front .footer-band{bottom:6px;height:14px;line-height:14px}
.envelope--back-white{left:413px;width:372px;background:var(--paper)}
.envelope--back-red{left:799px;width:377px;background:linear-gradient(135deg,var(--red),var(--red-dark) 85%)}
.envelope .flap{position:absolute;left:0;top:0;width:100%;height:70px}
.envelope .flap-brand{position:absolute;left:0;right:0;top:14px;justify-content:center;font-size:9px}
.envelope .flap-brand .dot{width:8px;height:8px}
.envelope--back-white .tone-area{left:0;right:0;top:70px;bottom:30px;background:linear-gradient(180deg,rgba(196,22,28,.06),rgba(196,22,28,0))}
.envelope--back-red .tone-area{left:0;right:0;top:70px;bottom:30px;background:linear-gradient(180deg,rgba(255,255,255,.08),rgba(255,255,255,0))}
.envelope .url{position:absolute;left:0;right:0;bottom:14px;text-align:center;font-size:6.8px}
.envelope--back-white .url{color:var(--grey)}
.envelope--back-red .url{color:#fff}
</style>
</head>
<body>

<!-- Letterhead, first version -->
<section class="item letterhead letterhead--one">
  <div class="tone-area" role="img" aria-label="Soft faint red brand decoration"></div>
  <div class="brand"><span class="dot"></span>BRANDVELLE</div>
  <div class="divider"></div>
  <div class="contact">
    <div class="row"><svg viewBox="0 0 10 10"><path d="M2 1h2l1 2-1 1a6 6 0 0 0 2 2l1-1 2 1v2c0 1-1 1-1 1A8 8 0 0 1 1 2s0-1 1-1z"/></svg>+61 3 5550 1827</div>
    <div class="row"><svg viewBox="0 0 10 10"><rect x="3" y="0.5" width="4" height="9" rx="1"/></svg>+61 455 016 342</div>
    <div class="row"><svg viewBox="0 0 10 10"><rect x="0.5" y="2" width="9" height="6"/></svg>sales@brandvelle-example.com.au</div>
    <div class="addr">Suite xxx, 212 Ferrow Lane<br>Melbourne, Victoria 3000</div>
  </div>
  <div class="letter-body">
    <p>Dear Client,</p>
    <p>Thank you for choosing us as your partner for branded merchandise. We supply pens, polo shirts, key rings, drink bottles, uniforms and bags for teams of every size across the country.</p>
    <p>Our team reviews each order with care and helps you select the right product, colour and print method so your logo looks sharp on every item.</p>
    <p>Browse our online range at any time to compare styles, check stock levels and request a quote. Samples can be sent to your office before any large run is placed.</p>
    <p>We work to clear timelines and keep you informed from artwork proof through to final delivery at your door.</p>
    <p>Please contact me directly if you have any questions about pricing or branding options.</p>
    <p>We look forward to working with you on your next promotion.</p>
  </div>
  <div class="signature"><div class="name">Yours Name</div><div class="role">Company Director</div></div>
  <div class="footer-band">www.brandvelle-example.com.au</div>
</section>

<!-- Letterhead, second version -->
<section class="item letterhead letterhead--two">
  <div class="brand"><span class="dot"></span>BRANDVELLE</div>
  <div class="divider"></div>
  <div class="contact">
    <div class="row"><svg viewBox="0 0 10 10"><path d="M2 1h2l1 2-1 1a6 6 0 0 0 2 2l1-1 2 1v2c0 1-1 1-1 1A8 8 0 0 1 1 2s0-1 1-1z"/></svg>+61 3 5550 1827</div>
    <div class="row"><svg viewBox="0 0 10 10"><rect x="3" y="0.5" width="4" height="9" rx="1"/></svg>+61 455 016 342</div>
    <div class="row"><svg viewBox="0 0 10 10"><rect x="0.5" y="2" width="9" height="6"/></svg>sales@brandvelle-example.com.au</div>
    <div class="addr">Suite xxx, 212 Ferrow Lane<br>Melbourne, Victoria 3000</div>
  </div>
  <div class="letter-body">
    <p>Dear Client,</p>
    <p>Thank you for choosing us as your partner for branded merchandise. We supply pens, polo shirts, key rings, drink bottles, uniforms and bags for teams of every size across the country.</p>
    <p>Our team reviews each order with care and helps you select the right product, colour and print method so your logo looks sharp on every item.</p>
    <p>Browse our online range at any time to compare styles, check stock levels and request a quote. Samples can be sent to your office before any large run is placed.</p>
    <p>We work to clear timelines and keep you informed from artwork proof through to final delivery at your door.</p>
    <p>Please contact me directly if you have any questions about pricing or branding options.</p>
    <p>We look forward to working with you on your next promotion.</p>
  </div>
  <div class="signature"><div class="name">Yours Name</div><div class="role">Company Director</div></div>
  <div class="footer-band">www.brandvelle-example.com.au</div>
</section>

<!-- Cover sheet -->
<section class="item cover">
  <div class="tone-area" role="img" aria-label="Soft translucent brand decoration"></div>
  <div class="brand brand--light"><span class="dot"></span>BRANDVELLE</div>
  <div class="url">www.brandvelle-example.com.au</div>
</section>

<!-- Business card front -->
<section class="item card card--front">
  <div class="brand"><span class="dot"></span>BRANDVELLE</div>
  <div class="divider"></div>
  <div class="person"><div class="name">DEREK HALLOWAY</div><div class="title">Account Manager</div></div>
  <div class="contact">
    <div class="row"><svg viewBox="0 0 10 10"><path d="M2 1h2l1 2-1 1a6 6 0 0 0 2 2l1-1 2 1v2c0 1-1 1-1 1A8 8 0 0 1 1 2s0-1 1-1z"/></svg>+61 3 5550 1827</div>
    <div class="row"><svg viewBox="0 0 10 10"><rect x="3" y="0.5" width="4" height="9" rx="1"/></svg>+61 455 016 342</div>
    <div class="row"><svg viewBox="0 0 10 10"><rect x="0.5" y="2" width="9" height="6"/></svg>sales@brandvelle-example.com.au</div>
    <div class="addr">Suite xxx, 212 Ferrow Lane<br>Melbourne, Victoria 3000</div>
  </div>
  <div class="footer-band">www.brandvelle-example.com.au</div>
</section>

<!-- Business card back, dark -->
<section class="item card card--dark">
  <div class="tone-area" role="img" aria-label="Brand symbol area in grey and red tones"></div>
  <div class="back-text">
    <div class="brand brand--light"><span class="dot"></span>BRANDVELLE</div>
    <div class="url">www.brandvelle-example.com.au</div>
  </div>
</section>

<!-- Business card back, red -->
<section class="item card card--red">
  <div class="tone-area" role="img" aria-label="Brand symbol area in grey and red tones"></div>
  <div class="back-text">
    <div class="brand brand--light"><span class="dot"></span>BRANDVELLE</div>
    <div class="url">www.brandvelle-example.com.au</div>
  </div>
</section>

<!-- DL envelope front -->
<section class="item envelope envelope--front">
  <div class="brand"><span class="dot"></span>BRANDVELLE</div>
  <div class="contact">
    <div class="row"><svg viewBox="0 0 10 10"><path d="M2 1h2l1 2-1 1a6 6 0 0 0 2 2l1-1 2 1v2c0 1-1 1-1 1A8 8 0 0 1 1 2s0-1 1-1z"/></svg>+61 3 5550 1827</div>
    <div class="row"><svg viewBox="0 0 10 10"><rect x="3" y="0.5" width="4" height="9" rx="1"/></svg>+61 455 016 342</div>
    <div class="row"><svg viewBox="0 0 10 10"><rect x="0.5" y="2" width="9" height="6"/></svg>sales@brandvelle-example.com.au</div>
    <div class="addr">Suite xxx, 212 Ferrow Lane<br>Melbourne, Victoria 3000</div>
  </div>
  <div class="window"></div>
  <div class="footer-band">www.brandvelle-example.com.au</div>
</section>

<!-- DL envelope back, white -->
<section class="item envelope envelope--back-white">
  <div class="tone-area" role="img" aria-label="Soft faint red brand decoration"></div>
  <svg class="flap" viewBox="0 0 372 70" preserveAspectRatio="none">
    <defs><linearGradient id="flapRed" x1="0" x2="1"><stop offset="0" stop-color="#7e0c10"/><stop offset=".5" stop-color="#c4161c"/><stop offset="1" stop-color="#7e0c10"/></linearGradient></defs>
    <path d="M0 0H372V14Q186 90 0 14Z" fill="url(#flapRed)"/>
  </svg>
  <div class="brand brand--light flap-brand"><span class="dot"></span>BRANDVELLE</div>
  <div class="url">www.brandvelle-example.com.au</div>
</section>

<!-- DL envelope back, red -->
<section class="item envelope envelope--back-red">
  <div class="tone-area" role="img" aria-label="Soft translucent brand decoration"></div>
  <svg class="flap" viewBox="0 0 377 70" preserveAspectRatio="none">
    <path d="M0 0H377V14Q188 90 0 14Z" fill="#6e0a0e" opacity=".55"/>
  </svg>
  <div class="brand brand--light flap-brand"><span class="dot"></span>BRANDVELLE</div>
  <div class="url">www.brandvelle-example.com.au</div>
</section>

</body>
</html>
```